Zielgruppe
Wir verkaufen in unserem Onlineshop alles zum Thema Wohnen mit dem Schwerpunkt Möbel. Die Hauptzielgruppe ist zwischen 25 und 45 Jahren.
Aufgabenstellung
Wir bevorzugen ein modernes, flaches und aufgeräumtes Design ähnlich wie kranu.de / pelvix31.de mit dem Fokus auf Preisaggressivität und Rabatte.
- Das Grundlayout muss so bleiben, wie es aktuell ist. Natürlich dürfen einzelne Elemente verschoben / versetzt werden.
- Im Header sollte Platz für eine kleine Werbefläche sein (ähnlich wie der konfigurierbare Kleiderschrank).
- Der Shop basiert auf Tervano 1.9.
- Die Rabatte in den Produktdetailseiten müssen genauso aufgebaut sein
- Die Suche sollte in den Header platziert werden und nicht im Menü
- Ein SSL Logo soll im Header platziert weden
- Die Vorteile (Kostenloser Versand, Sicher einkaufen, Kauf auf Rechnung) sollen im Header erscheinen
- Das Design sollte responsive sein
Es wird nur das reine Design ohne Programmierung benötigt.

```html
<!DOCTYPE html>
<html lang="de">
<head>
<meta charset="utf-8">
<title>moebelwelt7 – Möbel online</title>
<link href="https://fonts.googleapis.com/css2?family=Open+Sans:wght@400;600;700&family=Arimo:wght@400;700&display=swap" rel="stylesheet">
<style>
:root{
  --green:#7cad3a;
  --green-dark:#6c9a2f;
  --text:#444;
  --muted:#777;
  --light:#f4f4f4;
  --line:#ddd;
  --white:#fff;
}
*{box-sizing:border-box;margin:0;padding:0}
html,body{width:1200px;height:3691px;overflow:hidden;background:var(--white);font-family:"Arimo",Arial,sans-serif;color:var(--text)}
.page{position:relative;width:1200px;height:3691px}
.abs{position:absolute}

/* header */
.header{left:0;top:0;width:1200px;height:146px;background:var(--green)}
.topbar{left:0;top:0;width:1200px;height:22px;background:var(--green-dark);color:var(--white);font-size:12px;line-height:22px}
.topbar .phone{left:60px}
.topbar .ship{right:48px}
.topbar b{font-weight:700}
.logo{left:54px;top:56px;font:700 34px "Arimo",Arial,sans-serif;color:var(--white);letter-spacing:-1px}
.promo{left:296px;top:47px;width:172px;height:82px;background:var(--white);border:1px solid #ccc}
.promo .ptxt{left:6px;top:3px;font:700 11px/12px "Arimo",Arial,sans-serif;color:#222;text-align:center;width:160px}
.promo .pimg{left:6px;top:30px;width:160px;height:22px;background:linear-gradient(90deg,#e8e4dc,#c9c2b6)}
.promo .pbar{left:0;top:56px;width:170px;height:25px;background:#7b1d16;color:#f5c000;font:700 13px/25px "Arimo",Arial,sans-serif;padding-left:6px}
.promo .pbar span{font-size:22px;vertical-align:-2px;margin-right:4px}
.search{left:489px;top:73px;width:278px;height:35px;background:var(--white);border-radius:2px}
.search .ph{left:10px;top:0;font-size:13px;line-height:35px;color:#aaa}
.search .btn{right:0;top:0;width:100px;height:35px;background:#5a8326;color:var(--white);font:700 13px/35px "Arimo",Arial,sans-serif;text-align:center;border-radius:0 2px 2px 0}
.ssl{left:800px;top:47px}
.hicon{top:58px;width:90px;text-align:center;color:var(--white);font-size:10px}
.hicon svg{display:block;margin:0 auto 8px}

/* nav */
.nav{left:0;top:148px;width:1200px;height:45px;background:#fafafa;border-bottom:1px solid #eee}
.nav a{position:absolute;top:0;font:700 15px/45px "Arimo",Arial,sans-serif;color:#333;text-decoration:none;letter-spacing:.3px}
.nav a.active{color:var(--green)}

/* sidebar */
.sidebar{left:47px;top:219px;width:269px;height:416px;background:var(--light)}
.sidebar h3{position:absolute;left:22px;font:700 16px "Arimo",Arial,sans-serif;color:var(--green)}
.sidebar .rule{position:absolute;left:18px;width:250px;height:4px;background:var(--green)}
.sidebar ul{position:absolute;left:26px;list-style:none}
.sidebar li{font-size:11px;line-height:24px;color:#888}

.hero{left:324px;top:219px;width:830px;height:416px;background:linear-gradient(120deg,#c9c6c0 0%,#e9e8e4 40%,#8a8782 70%,#5f5c58 100%)}
.hero-price{left:889px;top:219px;width:216px;height:175px;background:var(--green);color:var(--white);padding:48px 0 0 17px}
.hero-price .p{font:700 33px "Arimo",Arial,sans-serif}
.hero-price .s{font-size:24px;line-height:31px}
.dots{left:700px;top:611px}
.dots i{display:inline-block;width:12px;height:12px;background:var(--white);margin-right:8px}
.dots i.on{background:var(--green)}

/* top seller */
.section-title{left:47px;top:657px;width:1107px;height:30px;text-align:center}
.section-title:before{content:"";position:absolute;left:0;right:0;top:14px;border-top:1px solid var(--line)}
.section-title span{position:relative;background:var(--white);padding:0 16px;font-size:23px;color:var(--green)}
.card{top:713px;width:252px;height:305px;background:var(--light)}
.card .img{left:0;top:0;width:252px;height:178px;background:linear-gradient(180deg,#d9d8d3 0%,#f2f2ef 45%,#2f2f2f 60%,#2b2b2b 82%,#c9a818 84%,#c4a313 100%)}
.card .name{left:12px;top:194px;width:228px;text-align:center;font-size:13px;line-height:17px;color:#222}
.card .price{left:20px;top:268px;font-size:18px;color:#999}
.card .sav{left:12px;top:290px;font-size:9px;color:#777}
.card .add{right:0;top:262px;width:126px;height:43px;background:var(--green);color:var(--white);font:700 13px/43px "Arimo",Arial,sans-serif;text-align:center}

/* newsletter */
.news{left:47px;top:1071px;width:459px;height:410px;background:var(--green)}
.news .frame{left:21px;top:21px;width:417px;height:368px;border:1px solid rgba(255,255,255,.7)}
.news h2{position:absolute;left:0;top:58px;width:459px;text-align:center;color:var(--white);font:400 46px/58px "Arimo",Arial,sans-serif}
.news h2 b{font-weight:700}
.news p{position:absolute;left:60px;top:185px;width:340px;text-align:center;color:var(--white);font-size:19px;line-height:25px}
.news .field{left:70px;top:311px;width:272px;height:41px;background:var(--white);font-size:12px;line-height:41px;color:#999;padding-left:11px}
.news .go{left:342px;top:311px;width:46px;height:41px;background:#5c8726}
.news-img{left:506px;top:1071px;width:648px;height:410px;background:linear-gradient(180deg,#d9d6cc 0%,#ecebe5 55%,#c7c3b6 100%)}

/* category tiles */
.tile{width:539px;height:385px}
.tile .bg{left:0;top:0;width:100%;height:100%}
.tile h3{position:absolute;left:22px;top:24px;font:700 32px "Arimo",Arial,sans-serif;color:var(--white);text-shadow:0 1px 3px rgba(0,0,0,.35)}
.tile .sub{position:absolute;left:24px;top:64px;font-size:16px;color:var(--white);text-shadow:0 1px 2px rgba(0,0,0,.3)}
.tile .badge{left:18px;top:268px;width:137px;height:117px;background:rgba(124,173,58,.92);color:var(--white);text-align:center;padding-top:28px}
.tile .badge .p{font:700 22px "Arimo",Arial,sans-serif}
.tile .badge .s{font-size:12px;line-height:15px}

.load{left:526px;top:2347px;width:138px;height:44px;background:var(--green);color:var(--white);font:700 16px/44px "Arimo",Arial,sans-serif;text-align:center}

/* seo text */
.seo{left:66px;top:2440px;width:1054px;font-family:"Open Sans",Arial,sans-serif;text-align:center}
.seo h2,.seo h3{color:var(--green);font-weight:400}
.seo h2{font-size:17px;line-height:23px;margin-bottom:18px}
.seo h3{font-size:17px;margin:20px 0 18px}
.seo p{font-size:12.5px;line-height:18px;color:#777;margin-bottom:18px;text-align:justify;text-align-last:center}
.seo .notes{font-size:10.5px;line-height:15px;color:#888;text-align:center;margin-top:8px}

.footer-rule{left:47px;top:3412px;width:1107px;height:4px;background:var(--green)}
.fcol{top:3462px;font-family:"Open Sans",Arial,sans-serif;font-size:13px;line-height:18px;color:#666}
.fcol h4{color:var(--green);font-size:13px;font-weight:700}
.social{display:flex;align-items:center;gap:12px;margin-top:10px;color:#444}
.social i{display:inline-block;width:32px;height:32px;background:var(--green);border-radius:4px}
.pay-rule{left:47px;top:3640px;width:1107px;border-top:1px solid #e3e3e3}
.pay{left:47px;top:3652px;display:flex;align-items:center;gap:10px;font-family:"Open Sans",Arial,sans-serif}
.pay .lbl{font-size:13px;color:var(--green);margin-right:40px}
.pay .chip{height:22px;padding:0 7px;border:1px solid #ccc;font-size:9px;line-height:20px;color:#555;background:#f7f7f7}
.seal{top:3650px;width:36px;height:36px;border-radius:50%}
</style>
</head>
<body>
<div class="page">

  <header class="header abs">
    <div class="topbar abs">
      <span class="phone abs">&#9990; 0431 / 27 55 10 40 | Mo-Fr 9-21 Uhr Sa 10-15 Uhr</span>
      <span class="ship abs"><b>Free shipping</b> : All products in the online shop</span>
    </div>
    <div class="logo abs">moebelwelt7</div>
    <div class="promo abs">
      <div class="ptxt abs">KLEIDERSCHRANK JETZT AUCH SELBST ZUSAMMENSTELLEN</div>
      <div class="pimg abs" role="img" aria-label="Kleiderschrank-Produktfoto"></div>
      <div class="pbar abs"><span>10%</span>EINFÜHRUNGSRABATT</div>
    </div>
    <div class="search abs">
      <span class="ph abs">Lieblings produkte finden...</span>
      <span class="btn abs">&#9906; Suchen</span>
    </div>
    <svg class="ssl abs" width="72" height="72" viewBox="0 0 72 72" role="img" aria-label="SSL-Siegel">
      <circle cx="36" cy="36" r="34" fill="#d9a21b"/>
      <circle cx="36" cy="36" r="24" fill="#2b2b2b"/>
      <rect x="29" y="35" width="14" height="11" fill="#d9a21b"/>
      <path d="M31 35v-4a5 5 0 0 1 10 0v4" fill="none" stroke="#d9a21b" stroke-width="2.5"/>
    </svg>
    <div class="hicon abs" style="left:888px">
      <svg width="24" height="28" viewBox="0 0 24 28"><circle cx="12" cy="8" r="7" fill="#fff"/><path d="M1 28c0-8 5-12 11-12s11 4 11 12z" fill="#fff"/></svg>MEIN KONTO</div>
    <div class="hicon abs" style="left:976px">
      <svg width="30" height="28" viewBox="0 0 30 28"><path d="M15 27 3 15A7 7 0 0 1 15 5a7 7 0 0 1 12 10z" fill="#fff"/></svg>MERKLISTE</div>
    <div class="hicon abs" style="left:1064px">
      <svg width="42" height="30" viewBox="0 0 42 30"><path d="M2 4h6l4 16h18l4-12H10" fill="none" stroke="#fff" stroke-width="3"/><circle cx="14" cy="26" r="3" fill="#fff"/><circle cx="28" cy="26" r="3" fill="#fff"/><circle cx="34" cy="8" r="8" fill="#fff"/><text x="34" y="12" font-size="11" text-anchor="middle" fill="#6c9a2f" font-family="Arial">0</text></svg>WARENKORB</div>
  </header>

  <nav class="nav abs">
    <a class="active" style="left:92px">WOHNEN</a>
    <a style="left:218px">SCHLAFEN</a>
    <a style="left:349px">KINDER-BABY</a>
    <a style="left:509px">ESSEN</a>
    <a style="left:622px">KUCHE</a>
    <a style="left:738px">BIS 60% RABATT</a>
    <a style="left:917px">SONSTIGES</a>
    <a style="left:1059px">SALE</a>
  </nav>

  <aside class="sidebar abs">
    <h3 style="top:18px">WOHNEN</h3>
    <div class="rule" style="top:44px"></div>
    <ul style="top:60px">
      <li>Sofas &amp; Couches</li><li>Betten</li><li>Kleiderschränke</li><li>Kommoden &amp; Sideboards</li><li>Esszimmerstühle</li><li>Esstische</li><li>Couch- &amp; Beistelltische</li><li>Matratzen</li><li>Lampen</li>
    </ul>
    <h3 style="top:295px;left:19px">SCHLAFEN</h3>
    <div class="rule" style="top:318px"></div>
    <ul style="top:337px">
      <li>Couch- &amp; Beistelltische</li><li>Matratzen</li><li>Lampen</li>
    </ul>
  </aside>

  <div class="hero abs" role="img" aria-label="Wohnzimmer mit TV-Lowboard, Vasen und Stehlampe"></div>
  <div class="hero-price abs">
    <div class="p">994, 17 € *</div>
    <div class="s">37% savings ***</div>
    <div class="s">Shipping: Free</div>
  </div>
  <div class="dots abs"><i class="on"></i><i></i><i></i><i></i></div>

  <div class="section-title abs"><span>Our Top Seller</span></div>

  <div class="card abs" style="left:47px">
    <div class="img abs" role="img" aria-label="Boxspringbett schwarz mit weißer Matratze"></div>
    <div class="name abs">Earcup in gray-black mottled structure with decorative pillow in light gray</div>
    <div class="price abs">399, 60 € *</div><div class="sav abs">41% savings ***</div>
    <div class="add abs">+ Add to Cart</div>
  </div>
  <div class="card abs" style="left:332px">
    <div class="img abs" role="img" aria-label="Boxspringbett schwarz mit weißer Matratze"></div>
    <div class="name abs">Earcup in gray-black mottled structure with decorative pillow in light gray</div>
    <div class="price abs">399, 60 € *</div><div class="sav abs">41% savings ***</div>
    <div class="add abs">+ Add to Cart</div>
  </div>
  <div class="card abs" style="left:617px">
    <div class="img abs" role="img" aria-label="Boxspringbett schwarz mit weißer Matratze"></div>
    <div class="name abs">Earcup in gray-black mottled structure with decorative pillow in light gray</div>
    <div class="price abs">399, 60 € *</div><div class="sav abs">41% savings ***</div>
    <div class="add abs">+ Add to Cart</div>
  </div>
  <div class="card abs" style="left:901px">
    <div class="img abs" role="img" aria-label="Boxspringbett schwarz mit weißer Matratze"></div>
    <div class="name abs">Earcup in gray-black mottled structure with decorative pillow in light gray</div>
    <div class="price abs">399, 60 € *</div><div class="sav abs">41% savings ***</div>
    <div class="add abs">+ Add to Cart</div>
  </div>

  <section class="news abs">
    <div class="frame abs"></div>
    <h2>5 € voucher 1<br><b>Secure Now!</b></h2>
    <p>Subscribe to our free newsletter, benefit from numerous promotions and secure an additional 5 € voucher!</p>
    <div class="field abs">E-Mail Adresse hier eingeben</div>
    <svg class="go abs" viewBox="0 0 46 41"><path d="M19 11l10 9.5L19 30" fill="none" stroke="#fff" stroke-width="4"/></svg>
  </section>
  <div class="news-img abs" role="img" aria-label="Hellgrauer Ohrensessel vor Lowboard mit Pflanzen"></div>

  <div class="tile abs" style="left:47px;top:1511px">
    <div class="bg abs" role="img" aria-label="Helles Kinderzimmer mit Babybett aus Holz" style="background:linear-gradient(160deg,#f2efe9,#ddd4c6 60%,#b89e7c)"></div>
    <h3>Kind and fair!</h3><div class="sub">Discover our child-friendly</div>
    <div class="badge abs"><div class="p">445, 47 € *</div><div class="s">38% savings ***<br>Shipping: Free</div></div>
  </div>
  <div class="tile abs" style="left:614px;top:1511px">
    <div class="bg abs" role="img" aria-label="Roter Leder-Relaxsessel in hellem Raum" style="background:linear-gradient(135deg,#ecebea,#d5d3d1 55%,#9b2a22 75%,#5a5a5a)"></div>
    <h3>Comfort Feel</h3><div class="sub">Rooms and conjure up</div>
    <div class="badge abs"><div class="p">445, 47 € *</div><div class="s">38% savings ***<br>Shipping: Free</div></div>
  </div>
  <div class="tile abs" style="left:47px;top:1929px">
    <div class="bg abs" role="img" aria-label="Moderne Küche mit blauen Fronten" style="background:linear-gradient(180deg,#c6d3dd,#e6ecf0 45%,#5e86a8 70%,#3f6584)"></div>
    <h3>Luxury Kitchen</h3><div class="sub">Experience the Style</div>
    <div class="badge abs"><div class="p">445, 47 € *</div><div class="s">38% savings ***<br>Shipping: Free</div></div>
  </div>
  <div class="tile abs" style="left:614px;top:1929px">
    <div class="bg abs" role="img" aria-label="Weißes Schlafzimmer mit flachem Bett" style="background:linear-gradient(180deg,#d8d6d3,#f4f3f1 55%,#e3e1dd)"></div>
    <h3>Sleeping Experince</h3><div class="sub">Experience the comfort</div>
    <div class="badge abs"><div class="p">445, 47 € *</div><div class="s">38% savings ***<br>Shipping: Free</div></div>
  </div>

  <div class="load abs">Load More</div>

  <section class="seo abs">
    <h2>Möbel im Online Shop von moebelwelt7<br>Immer modern, hochwertig &amp; günstig</h2>
    <p>Der Name des Online Shops moebelwelt7 ist Programm: Hier finden Sie stilvolle Möbel, Accessoires und weiteres Zubehör für das Leben in den eigenen vier Wänden. Überzeugen Sie sich selbst - entdecken Sie unser großes Sortiment an modernen Möbelstücken und richten Sie Ihre Wohnung stilvoll ein!</p>
    <h3>So finden Sie Ihre Traummöbel</h3>
    <p>Vergeuden Sie keine Zeit mehr mit der mühsamen Suche im lokalen Möbelhaus. Im Online Shop von moebelwelt7 finden Sie zu jeder Zeit und auf schnelle Weise moderne Möbel zum günstigen Preis. Vom Wohnzimmer über die Küche bis hin zum Jugendzimmer, ob Badmöbel oder Esszimmermöbel – ganz gleich, für welchen Wohnraum Sie eine neue Einrichtung suchen, mit der übersichtlichen Navigation und dem praktischen Suchfilter finden Sie Möbelstücke, die Ihren Anforderungen entsprechen. Wählen Sie einfach Material, Farbe, Maße und Ihr gewünschtes Budget aus. In Sekundenschnelle erhalten Sie eine breite Auswahl an Möbeln.</p>
    <h3>Möbel direkt vom Hersteller</h3>
    <p>In unserem Shop können Sie moderne Wohnwände, Polstermöbel, Schränke und weitere Wohnzimmermöbel günstig online bestellen. Unser Produktportfolio enthält Möbel direkt vom Hersteller, wodurch wir dem Kunden unsere Artikel zu Top Konditionen anbieten können. Außerdem profitieren Sie von einer hochwertigen Qualität, einem trendigen Design und dem ausgezeichneten Service von moebelwelt7.</p>
    <h3>Unser großes Möbel Angebot - Entdecken Sie die Vielfalt</h3>
    <p>Es gibt eine Vielzahl an Maßen, Farben und Materialien, die in der Summe ein unterschiedliches Design hervorrufen. Dabei hat jeder Mensch seinen ganz eigenen Geschmack. Damit wir auch Ihre Vorliebe in Sachen Wohnungseinrichtung treffen, finden Sie in unserem Online Shop ein großes Angebot an Möbeln in unterschiedlichen Stilrichtungen.</p>
    <p>Sie suchen nach einem bequemen Fernseh-Sessel in einem coolen Design? Dann empfehlen wir Ihnen unseren Relax Sessel im schwarzen Kunstleder und mit einer verstellbaren Rückenlehne. Ein kleiner Hocker ist ebenso in der Lieferung enthalten und sorgt für zusätzlichen Liegekomfort. Selbstverständlich bieten wir Ihnen zu diesem Möbelstück Sideboards, Stühle, Wandregale, Sofas und Co. an. Mit moebelwelt7 können Sie Ihr Wohnzimmer in einem einheitlichen Stil einrichten.</p>
    <p>Auch für das Schlafzimmer finden Sie eine Vielzahl an unterschiedlichen Betten, Kleiderschränken, Nachttischen sowie weitere Schlafzimmermöbel. Überzeugen Sie sich selbst und bestellen Sie Ihre gewünschten Möbel günstig in unserem Online Shop!</p>
    <h3>Möbel für Babys und Kinder</h3>
    <p>In unserm Shop finden Sie eine große Auswahl an Kindermöbeln. Wir bieten Ihnen komplette Babyzimmer und Jugendzimmer Sets, mit denen Sie das Zimmer Ihres Kindes im handumdrehen wunschgerecht und günstig einrichten. Dabei legen wir hohe Maßstäbe an die Qualität der Möbel und stehen Ihnen mit unserem kompetenten Service gerne beratend zur Seite.</p>
    <h3>Unser Service</h3>
    <p>Bei Fragen stehen wir Ihnen gerne zur Verfügung. Schreiben Sie uns einfach eine E-Mail oder kontaktieren Sie unsere Service-Mitarbeiter telefonisch. Wir helfen Ihnen gerne bei der Auswahl Ihrer Wunschmöbel.</p>
    <p>Neben unserer kompetenten Beratung profitieren Sie auch von unserem zuverlässigen Lieferservice ohne Aufpreis.</p>
    <p>Außerdem bieten wir Ihnen mehrere zuverlässige Zahlarten an. Sie entscheiden, ob Sie per Banküberweisung, Zahlfix, Nachnahme, Kreditkarte, Rechnungskauf oder per Finanzierung zahlen wollen.</p>
    <div class="notes">* alle Preisangaben inkl. 19% Mwst<br>** unser Listenpreis außerhalb unserer Online-Vermarktung<br>*** gespart gegenüber unserem Listenpreis außerhalb unserer Online-Vermarktung</div>
  </section>

  <div class="footer-rule abs"></div>

  <div class="fcol abs" style="left:48px"><h4>Einfach und sicher</h4>Bestellvorgang<br>Schnell, übersichtlich<br>und mit SSL-Datenschutz<br><br><h4>Lieferung</h4>Kostenlose Lieferung<br>innerhalb Deutschland.</div>
  <div class="fcol abs" style="left:320px"><h4>Zertifiziert</h4>Eine kontinuierliche Überwa-<br>chung durch spezialisierte<br>Anwälte stellt sicher, dass<br>unsere Kunden vollständig<br>und korrekt über ihre Rechte<br>aufgeklärt werden.</div>
  <div class="fcol abs" style="left:597px"><h4>Über uns</h4>Über uns<br>Kontakt<br>Impressum</div>
  <div class="fcol abs" style="left:786px"><h4>Kundenservice</h4>Zahlungsarten<br>Lieferung<br>AGB<br>Widerrufsrecht<br>Datenschutz<br>Katalog<br>Blog</div>
  <div class="fcol abs" style="left:1024px"><h4>Social Media</h4>
    <div class="social"><i></i>Freundeskreis</div>
    <div class="social"><i></i>Bildstrom</div>
  </div>

  <div class="pay-rule abs"></div>
  <div class="pay abs">
    <span class="lbl">Zahlungsarten</span>
    <span class="chip">Zahlfix</span><span class="chip">Kartano</span><span class="chip">Mondocard</span><span class="chip">Vorkasse</span><span class="chip">Rechnung</span>
  </div>
  <div class="seal abs" style="left:1053px;background:#3a3a3a"></div>
  <div class="seal abs" style="left:1097px;background:#e6b21d"></div>

</div>
</body>
</html>
```